Wordpress design for media production company

We are a small production company called Copper Lantern Films specializing in documentary and short film.

We are after a wordpress web site that is fun and engaging with a relaxed feel. We would like to be able to easily edit and maintain the website ourselves.

We would like:
* A title screen that has a photo taking up most of the screen.
* Contact details (inc. social media links) on a static bar at the bottom.
* An area for our previous work. Some thumbnails or icons that open up and embedded youtube or vimeo video.
* An area for "about us" which will have information on the company and links to separate profiles of 3 (initially) employees.
* A Blog.
* Somewhere to show what we are currently working on.
* Examples of other stuff we have done (ie. photography, poetry, audio, animation and VFX).

We already have a logo that can be animated. It would be very cool to have it as a "Loading" page while things load in the background.

The text needs to be fun but easy to read.

We already have a license for "Q Layout" which seems pretty cool and flexible, so if you wanted to use it then great but if not then that is fine too.

A couple of pages that we like are:
http://www.plumorchardworks.com/
http://dorianvelkot.com/
http://www.spinthegrove.com/

Please do not hesitate to contact me if you would like more information on anything.

Cheers

Gideon

Target Market(s)

Mainly Australian clients seeking media services
Broadcasting companies

Industry/Entity Type

It Company

Requirements
Nice to have
• I love the parallax look on http://www.plumorchardworks.com/

```html
<!DOCTYPE html>
<html lang="en">
<head>
<meta charset="utf-8">
<title>Copper Lantern Films</title>
<link rel="stylesheet" href="https://fonts.googleapis.com/css2?family=Open+Sans:ital,wght@0,300;0,400;0,600;0,700;1,700&display=swap">
<style>
:root{
  --ink:#333333;
  --muted:#555555;
  --black:#000000;
  --bar:#1e1e1e;
  --white:#ffffff;
  --brand-red:#8e0b0b;
  --name-red:#c40000;
  --rule:#9a9a9a;
  --dot:#555555;
}
*{margin:0;padding:0;box-sizing:border-box}
html,body{width:1200px;height:2917px;overflow:hidden}
body{position:relative;background:var(--white);font-family:"Open Sans",Arial,sans-serif;color:var(--ink)}

/* header */
.site-header{position:absolute;left:0;top:0;width:1200px;height:502px;background:var(--black)}
.brand{position:absolute;left:150px;top:18px;width:110px;text-align:center;color:var(--white)}
.brand-mark{display:block;width:62px;height:62px;margin:0 auto 5px;border:3px solid var(--white);border-radius:50%}
.brand-name{font-size:11px;font-weight:700;line-height:13px}
.social{position:absolute;left:957px;top:26px;display:flex;gap:4px}
.social span{width:27px;height:27px;border-radius:50%;background:#7a7a7a}
.main-nav{position:absolute;top:68px;left:408px;width:640px;height:26px;font-size:16px;color:var(--white)}
.main-nav a{position:absolute;top:0;color:var(--white);text-decoration:none;white-space:nowrap}
.hero{position:absolute;left:156px;top:130px;width:888px;height:319px;
  background:linear-gradient(to bottom,#5a6c8e 0%,#b7a774 28%,#f3cd45 44%,#d8c640 54%,#8ea32c 70%,#4f6b18 100%)}
.dots{position:absolute;top:472px;left:568px;display:flex;gap:4px}
.dots span{width:12px;height:12px;border-radius:50%;background:var(--dot)}
.dots span.on{background:#b00000}

/* section headings */
.section-title{position:absolute;left:0;width:1200px;text-align:center;font-size:31px;font-weight:300;color:var(--ink)}
.ruled-title{position:absolute;left:161px;width:874px;font-size:30px;font-weight:300;color:var(--ink);border-bottom:2px solid var(--rule);padding-bottom:2px;line-height:40px}

.body-copy{font-size:12.4px;line-height:22.4px;color:var(--muted)}

.about-intro{position:absolute;left:165px;top:606px;width:870px;text-align:center}

/* team */
.member{position:absolute;top:772px;width:285px}
.member .portrait{position:absolute;left:0;top:0;width:125px;height:125px;border-radius:50%}
.member .name{position:absolute;left:135px;top:50px;font-size:18px;font-weight:700;color:var(--name-red);white-space:nowrap}
.member .role{position:absolute;left:135px;top:75px;font-size:12px;color:#666}
.member .bio{position:absolute;left:0;top:129px;width:282px}

/* cards */
.card{position:absolute;width:278px}
.card .thumb{position:relative;width:278px}
.btn{display:inline-block;background:var(--brand-red);color:var(--white);font-size:12px;font-weight:700;width:101px;height:33px;line-height:33px;text-align:center}
.player-bar{position:absolute;left:0;bottom:0;width:100%;height:14px;background:#1b1b1b}
.player-bar i{position:absolute;left:30px;right:60px;top:5px;height:4px;background:#3f7fb0}
.play{position:absolute;left:50%;top:50%;transform:translate(-50%,-60%)}

/* blog */
.post{position:absolute;left:165px;width:870px}
.post .photo{position:absolute;left:0;top:0;width:278px;height:214px}
.post .headline{position:absolute;left:304px;top:-4px;width:566px;font-size:16.5px;line-height:24px;font-weight:700;color:var(--ink)}
.post .meta{position:absolute;left:304px;top:58px;font-size:12.5px;font-weight:600;color:#222}
.post .excerpt{position:absolute;left:304px;top:84px;width:566px}
.more{color:var(--brand-red);font-weight:700;font-style:italic}

/* tabs */
.tabs{position:absolute;left:165px;top:2482px;width:868px;height:56px;background:var(--bar);font-size:16px;color:var(--white)}
.tab{position:absolute;top:0;height:56px;line-height:56px}
.tab.active{left:0;width:168px;background:var(--brand-red);text-align:center}
.tab-pointer{position:absolute;left:228px;top:2538px}
.gallery-item{position:absolute;top:2564px;width:278px}
.gallery-item .shot{width:278px;height:198px}
.gallery-item p{font-size:12.4px;color:var(--muted);margin-top:12px}

/* footer */
.site-footer{position:absolute;left:0;top:2828px;width:1200px;height:89px;background:var(--black);color:var(--white);text-align:center}
.footer-nav{margin-top:25px;font-size:12.5px}
.footer-nav span{margin:0 10px}
.copyright{font-size:12.5px;margin-top:10px}
</style>
</head>
<body>

<header class="site-header">
  <div class="brand">
    <span class="brand-mark"></span>
    <div class="brand-name">Copper Lantern Films</div>
  </div>
  <div class="social" aria-label="Social links"><span></span><span></span><span></span></div>
  <nav class="main-nav">
    <a style="left:0">Home</a>
    <a style="left:76px">About Us</a>
    <a style="left:183px">Blog</a>
    <a style="left:251px">Our Previous Work</a>
    <a style="left:426px">Recent Works</a>
    <a style="left:555px">Contact Us</a>
  </nav>
  <div class="hero" role="img" aria-label="Man with raised arms in a grass field at sunset"></div>
  <div class="dots"><span class="on"></span><span></span><span></span><span></span></div>
</header>

<h2 class="section-title" style="top:538px">About Us</h2>
<p class="about-intro body-copy">Lorem Ipsum is simply dummy text of the printing and typesetting industry. Lorem Ipsum has been the industry's standard dummy text ever since the 1500s, when an unknown printer took a galley of type and scrambled it to make a type specimen book. It has survived not only five centuries, but also the leap into electronic typesetting, remaining essentially unchanged. It was popularised in the 1960s with the release of Tessaline sheets containing Lorem Ipsum passages, and more recently with desktop publishing software like Folio Setter including versions of Lorem Ipsum.<br>Lorem Ipsum is simply dummy text of the printing and typesetting industry.</p>

<div class="member" style="left:167px">
  <div class="portrait" role="img" aria-label="Team member portrait" style="background:radial-gradient(circle at 50% 45%,#e8c9a4,#8aa46a)"></div>
  <div class="name">Marla Quenby</div><div class="role">Copper Lantern Films</div>
  <p class="bio body-copy">Lorem Ipsum is simply dummy text of the printing and typesetting industry. Lorem Ipsum has been the industry's standard dummy text ever since the 1500s, when an unknown printer took &nbsp;essentially unchanged.</p>
</div>
<div class="member" style="left:461px">
  <div class="portrait" role="img" aria-label="Team member portrait" style="background:radial-gradient(circle at 50% 55%,#d52a1e,#f3b77a)"></div>
  <div class="name">Marla Quenby</div><div class="role">Copper Lantern Films</div>
  <p class="bio body-copy">Lorem Ipsum is simply dummy text of the printing and typesetting industry. Lorem Ipsum has been the industry's standard dummy text ever since the 1500s, when an unknown printer took &nbsp;essentially unchanged.</p>
</div>
<div class="member" style="left:757px">
  <div class="portrait" role="img" aria-label="Team member portrait" style="background:radial-gradient(circle at 45% 50%,#7a4e3a,#d6d6d6)"></div>
  <div class="name">Marla Quenby</div><div class="role">Copper Lantern Films</div>
  <p class="bio body-copy">Lorem Ipsum is simply dummy text of the printing and typesetting industry. Lorem Ipsum has been the industry's standard dummy text ever since the 1500s, when an unknown printer took &nbsp;essentially unchanged.</p>
</div>

<h2 class="section-title" style="top:1067px">Our Previous Work</h2>

<div class="card" style="left:165px;top:1134px">
  <div class="thumb" role="img" aria-label="Video still of a woman on a swing at sunset" style="height:206px;background:linear-gradient(135deg,#5a3a1c,#f0b23c 45%,#b77ab8 100%)">
    <svg class="play" width="44" height="44" viewBox="0 0 44 44"><circle cx="22" cy="22" r="21" fill="#222" fill-opacity=".75" stroke="#ddd" stroke-width="2"/><path d="M17 13 L31 22 L17 31 Z" fill="#fff"/></svg>
    <div class="player-bar"><i style="background:#b03030"></i></div>
  </div>
  <p class="body-copy" style="margin-top:16px">Lorem Ipsum is simply dummy text of the printing and typesetting industry. Lorem Ipsum has been the industry's standard dummy text</p>
  <span class="btn" style="margin-top:12px">Read More</span>
</div>
<div class="card" style="left:461px;top:1134px">
  <div class="thumb" role="img" aria-label="Video still of a smiling woman in an apron" style="height:206px;background:linear-gradient(135deg,#6f8a4c,#d9b9a0 45%,#2b3340 75%,#c45a6a)">
    <svg class="play" width="56" height="40" viewBox="0 0 56 40"><rect width="56" height="40" rx="6" fill="#111" fill-opacity=".8"/><path d="M22 11 L36 20 L22 29 Z" fill="#fff"/></svg>
    <div class="player-bar"><i></i></div>
  </div>
  <p class="body-copy" style="margin-top:16px">Lorem Ipsum is simply dummy text of the printing and typesetting industry. Lorem Ipsum has been the industry's standard dummy text</p>
  <span class="btn" style="margin-top:12px">Read More</span>
</div>
<div class="card" style="left:757px;top:1134px">
  <div class="thumb" role="img" aria-label="Video still of a smiling family" style="height:206px;background:linear-gradient(135deg,#cfd9e4,#e3b393 40%,#5b8fc4 80%)">
    <svg class="play" width="56" height="40" viewBox="0 0 56 40"><rect width="56" height="40" rx="6" fill="#111" fill-opacity=".8"/><path d="M22 11 L36 20 L22 29 Z" fill="#fff"/></svg>
    <div class="player-bar"><i></i></div>
  </div>
  <p class="body-copy" style="margin-top:16px">Lorem Ipsum is simply dummy text of the printing and typesetting industry. Lorem Ipsum has been the industry's standard dummy text</p>
  <span class="btn" style="margin-top:12px">Read More</span>
</div>

<h2 class="ruled-title" style="top:1524px">Blog</h2>

<article class="post" style="top:1589px">
  <div class="photo" role="img" aria-label="Woman meditating on a beach" style="background:linear-gradient(to bottom,#e9d9c3,#c9b8a4 45%,#8fa4b0 60%,#d8c1a0)"></div>
  <h3 class="headline">Lorem Ipsum is simply dummy text of the printing and typesetting industry. Lorem Ipsum has been the industry's</h3>
  <div class="meta">March &nbsp;22-2013 Posted By Copper Lantern Films</div>
  <p class="excerpt body-copy">Ever since the 1500s, when an unknown printer took a galley of type and scrambled it to make a type specimen book. It has survived not only five centuries, but also the leap into electronic typesetting, remaining essentially unchanged. It was popularised in the 1960s with the release of Tessaline sheets containing Lorem Ipsum passages, and more recently with desktop publishing software like Folio Setter including versions of Lorem Ipsum. emaining essentially unchanged... <span class="more">Read More</span></p>
</article>

<article class="post" style="top:1852px">
  <div class="photo" role="img" aria-label="Two runners outdoors" style="background:linear-gradient(120deg,#2d7d9c,#c94a3a 35%,#e8c7a8 55%,#f4f4f4 75%,#5d8f3a)"></div>
  <h3 class="headline">Lorem Ipsum is simply dummy text of the printing and typesetting industry. Lorem Ipsum has been the industry's</h3>
  <div class="meta">March &nbsp;22-2013 Posted By Copper Lantern Films</div>
  <p class="excerpt body-copy">Ever since the 1500s, when an unknown printer took a galley of type and scrambled it to make a type specimen book. It has survived not only five centuries, but also the leap into electronic typesetting, remaining essentially unchanged. It was popularised in the 1960s with the release of Tessaline sheets containing Lorem Ipsum passages, and more recently with desktop publishing software like Folio Setter including versions of Lorem Ipsum. emaining essentially unchanged... <span class="more">Read More</span></p>
</article>

<h2 class="ruled-title" style="top:2115px">Recent Works</h2>

<div class="card" style="left:165px;top:2194px">
  <div class="thumb" role="img" aria-label="Older couple laughing on a beach" style="height:130px;background:linear-gradient(to bottom,#a9c6e0,#e6d2c0 55%,#d4b79a)"></div>
  <p class="body-copy" style="margin-top:14px">Lorem Ipsum is simply dummy text of the printing and typesetting industry. Lorem Ipsum has been the industry's standard dummy text</p>
  <span class="btn" style="margin-top:12px">Read More</span>
</div>
<div class="card" style="left:461px;top:2194px">
  <div class="thumb" role="img" aria-label="Happy family with children" style="height:130px;background:linear-gradient(120deg,#f2f2f2,#8a5a3c 35%,#d64a7a 60%,#5a3a2a 85%,#eeeeee)"></div>
  <p class="body-copy" style="margin-top:14px">Lorem Ipsum is simply dummy text of the printing and typesetting industry. Lorem Ipsum has been the industry's standard dummy text</p>
  <span class="btn" style="margin-top:12px">Read More</span>
</div>
<div class="card" style="left:757px;top:2194px">
  <div class="thumb" role="img" aria-label="Woman leaping with a blue fabric against the sky" style="height:130px;background:linear-gradient(135deg,#1d5fb8,#3a86d6 50%,#9cc6ea)"></div>
  <p class="body-copy" style="margin-top:14px">Lorem Ipsum is simply dummy text of the printing and typesetting industry. Lorem Ipsum has been the industry's standard dummy text</p>
  <span class="btn" style="margin-top:12px">Read More</span>
</div>

<div class="tabs">
  <div class="tab active">Photography</div>
  <div class="tab" style="left:193px">Poetry</div>
  <div class="tab" style="left:292px">Audio</div>
  <div class="tab" style="left:397px">Animation</div>
  <div class="tab" style="left:525px">VFX</div>
</div>
<svg class="tab-pointer" width="18" height="12" viewBox="0 0 18 12"><path d="M0 0 H18 L9 12 Z" fill="#8e0b0b"/></svg>

<div class="gallery-item" style="left:165px">
  <div class="shot" role="img" aria-label="Parents holding a toddler" style="background:linear-gradient(120deg,#8fae5a,#e2b08a 40%,#3a4a6a 70%,#d9c3a5)"></div>
  <p>Lorem Ipsum is simply dummy text</p>
</div>
<div class="gallery-item" style="left:461px">
  <div class="shot" role="img" aria-label="Person in a white shirt holding their back" style="background:linear-gradient(120deg,#dcdcdc,#f2efe9 45%,#c8a88a 70%,#eeeeee)"></div>
  <p>Lorem Ipsum is simply dummy text</p>
</div>
<div class="gallery-item" style="left:757px">
  <div class="shot" role="img" aria-label="Bicycle wheel on a dusty trail at sunset" style="background:linear-gradient(135deg,#f6c04a,#e27a1e 45%,#8a3410)"></div>
  <p>Lorem Ipsum is simply dummy text</p>
</div>

<footer class="site-footer">
  <div class="footer-nav">Home<span>|</span>About Us<span>|</span>Blog<span>|</span>Our Previous Work<span>|</span>Recent Works<span>|</span>Contact Us</div>
  <div class="copyright">© 2014 Company Name,All Rights reserved</div>
</footer>

</body>
</html>
```